Large online photo magazine needs redesign

We have previously digitised a historical photographic magazine of around 20,000 printed pages and made it available online. The magazine ran up to the early 1970s, and the content is largely black and white photographs of local events, accompanied by short captions.

Although the content is very rich, the design needs to be revisited so that:
* it is visually appealing
* it is responsive (i.e. works in browsers across all manner of devices)
* is faithful to the nature of the content

There are only a few core page types, and the central one is the article page, an example of which can be seen at:
http://snapgazette.example/gisborne/issue/KLR48_19600714/t1-body-d4.html

Any design submitted should be based on the treatment of an article page such as the above.

Given the large number of pages on our site, we need a design which can be templated to work for any content in the collection, i.e. we cannot hand-craft our templates to match a given page of content, rather a template must work acceptably well for all content.

The current site, although basic in design, has the advantage that it is quite efficient in the amount of data per page request (around 100k - 200k). While not adverse to web fonts, banner imagery etc, we will carefully consider the benefit gained from any such treatment against the amount of extra data that needs to be downloaded to the client's browser.

For the right design, we are able ourselves to adapt it to a CSS layout.

An example of each core page type is as follows (though for this project we only expect a design for a single page, as itemised above):

http://snapgazette.example/gisborne/index.html
http://snapgazette.example/gisborne/about.html
http://snapgazette.example/gisborne/help.html
http://snapgazette.example/gisborne/initial/index.html
http://snapgazette.example/gisborne/search/results?type=section&text=smith&cmdSubmit=Go
http://snapgazette.example/gisborne/advanced-search/index.html
http://snapgazette.example/gisborne/issue/KLR48_19600714/t1-front-d1.html
http://snapgazette.example/gisborne/issue/KLR48_19600714/index.html
http://snapgazette.example/gisborne/issue/KLR48_19600714/fig-KLR48_19600714_005a.html
http://snapgazette.example/gisborne/issue/KLR48_19600714/KLR48_19600714_012.html
http://snapgazette.example/gisborne/issue/KLR48_19600714/thumbnails.html

Target Market(s)

A general browsing audience of all ages, but skewed towards the older generations, and those interested in family / regional history.

The average user will not be particularly web-savy, and the treatment of the content should not detract / distract from the actual content itself.

Industry/Entity Type

Events

Requirements
Must have
• * it is visually appealing
The content should be visually appealing to the audience, which can be defined as a general browsing audience of all ages, but skewed towards the middle and older generations.

* it is responsive (the design can be adapted - by us - to work in browsers across all manner of devices)

The magazine covers (http://snapgazette.example/gisborne/issues/index.html) offer some possible inspiration for treatment of the material.

```html
<!DOCTYPE html>
<html lang="en">
<head>
<meta charset="utf-8">
<title>Flying Sisters from Gisborne – Snap Gazette</title>
<link rel="stylesheet" href="https://fonts.googleapis.com/css2?family=Open+Sans:wght@400;600;700&display=swap">
<style>
:root{
  --brand:#c8394b;
  --brand-dark:#a82d3d;
  --ink:#222;
  --muted:#444;
  --rule:#8a8a8a;
  --white:#fff;
  --sepia-light:#e9e3cf;
  --sepia-dark:#3b3630;
}
*{box-sizing:border-box;margin:0;padding:0}
html,body{width:1200px;height:1181px;overflow:hidden;background:var(--white)}
body{font-family:"Open Sans",sans-serif;color:var(--ink);position:relative}
a{color:inherit;text-decoration:none}
.masthead{position:absolute;left:0;top:0;width:1200px;height:86px;background:var(--brand)}
.brand-name{position:absolute;left:171px;top:18px;font-size:40px;font-weight:700;color:var(--white);letter-spacing:1px;line-height:50px}
.search-box{position:absolute;left:798px;top:20px;width:230px;height:23px;border:1px solid #f3c6cc;color:#fbe4e7;font-size:12px;padding:3px 6px;display:flex;justify-content:space-between;align-items:center}
.advanced-search{position:absolute;right:172px;top:47px;color:var(--white);font-size:12px;font-weight:600}
.breadcrumb{position:absolute;right:172px;top:90px;font-size:12px;color:var(--ink)}
.breadcrumb .sep{color:var(--brand);margin:0 3px}
.main-nav{position:absolute;left:0;top:109px;width:1200px;height:28px;background:var(--brand);color:var(--white);font-size:12px;font-weight:600}
.main-nav ul{list-style:none;position:absolute;top:6px;display:flex}
.main-nav .primary{left:171px}
.main-nav .secondary{right:172px}
.main-nav li+li::before{content:"|";margin:0 16px;font-weight:400}
.article-title{position:absolute;left:170px;top:156px;font-size:18px;font-weight:600;color:var(--brand);letter-spacing:.2px}
.issue-date{position:absolute;left:171px;top:180px;font-size:12.5px;font-weight:600}
.pager{position:absolute;left:640px;top:160px}
.print-link{position:absolute;left:631px;top:182px;font-size:11.5px}
.photo-frame{position:absolute;border:1px solid var(--rule);padding:5px;background:var(--white)}
.photo{width:100%;height:100%}
.photo.sepia{background:linear-gradient(160deg,#d9d3bd,#5b5448 55%,#2e2a26)}
.photo.sepia-group{background:linear-gradient(180deg,#cfc8b2 0%,#39342f 45%,#2b2825 70%,#e4dcc4 72%,#e9e3cf 100%)}
.photo.sepia-scene{background:linear-gradient(180deg,#d8d2bc 0%,#8b8576 40%,#5e594f 55%,#c9c2a9 80%)}
.caption-text{position:absolute;left:415px;width:300px;font-size:12.4px;line-height:17.2px;color:var(--ink)}
.section-heading{position:absolute;left:415px;top:754px;font-size:17px;font-weight:400;letter-spacing:.5px;color:var(--ink)}
.pointer{position:absolute}
.divider{position:absolute;left:738px;top:137px;width:1px;height:959px;background:var(--rule)}
.side-title{position:absolute;left:757px;top:156px;font-size:18px;font-weight:600;color:var(--brand)}
.page-thumb{position:absolute;left:757px;top:214px;width:214px;height:138px;background:linear-gradient(90deg,#c9c2ae,#6f695d 30%,#d3ccb7 50%,#5c574e 75%,#bab39e)}
.view-page{position:absolute;left:758px;top:360px;font-size:12.4px}
.issue-tree{position:absolute;left:758px;top:394px;font-size:12.4px}
.issue-tree .root{font-weight:600;padding-left:14px;position:relative}
.issue-tree .line{position:absolute;left:0;top:3px;width:1px;height:176px;background:#555}
.issue-tree ul{list-style:none;margin-top:2px}
.issue-tree li{display:flex;align-items:center;height:27.4px;padding-left:10px}
.issue-tree li svg{margin-right:4px}
.cover{position:absolute;width:129px}
.cover-art{height:172px;border-top:16px solid var(--brand);border-bottom:8px solid var(--brand)}
.cover-label{font-size:11px;font-weight:600;margin-top:6px;white-space:nowrap}
.footer-rule{position:absolute;left:0;top:1096px;width:1200px;height:1px;background:var(--rule)}
.licence-badge{position:absolute;left:562px;top:1113px;width:76px;height:26px;background:#cfcfcf;border:2px solid #111}
.copyright{position:absolute;left:0;width:1200px;top:1145px;text-align:center;font-size:12.4px}
.build-code{position:absolute;left:0;width:1200px;top:1163px;text-align:center;font-size:12px;color:var(--brand)}
</style>
</head>
<body>
<header class="masthead">
  <a class="brand-name" href="http://snapgazette.example/gisborne/index.html">Snap Gazette</a>
  <div class="search-box"><span>Search Snap Gazette</span>
    <svg width="12" height="12" viewBox="0 0 12 12" fill="none" stroke="#fff" stroke-width="1.4"><circle cx="7" cy="5" r="3.6"/><path d="M4.4 7.6 1 11"/></svg>
  </div>
  <a class="advanced-search" href="http://snapgazette.example/gisborne/advanced-search/index.html">ADVANCED SEARCH</a>
</header>

<div class="breadcrumb">Snap Gazette<span class="sep">›</span>Issues<span class="sep">›</span>KLR48_19600714<span class="sep">›</span>KLR48_19600714_003</div>

<nav class="main-nav">
  <ul class="primary"><li>HOME</li><li>ABOUT</li><li>BROWSE SNAP GAZETTE</li><li>A-Z PEOPLE</li></ul>
  <ul class="secondary"><li>HELP</li><li>REPORT AN ERROR</li></ul>
</nav>

<main>
  <h1 class="article-title">FLYING SISTERS FROM GISBORNE</h1>
  <p class="issue-date">No.48 July 14, 1960</p>
  <svg class="pager" width="72" height="16" viewBox="0 0 72 16" fill="var(--brand)" stroke="var(--brand)">
    <rect x="0" y="2" width="2.4" height="12" stroke="none"/><path d="M11 2 3 8l8 6z" stroke="none"/>
    <path d="M30 2 24 8l6 6" fill="none" stroke-width="2.4"/>
    <path d="M46 2l6 6-6 6" fill="none" stroke-width="2.4"/>
    <path d="M61 2l8 6-8 6z" stroke="none"/><rect x="69.6" y="2" width="2.4" height="12" stroke="none"/>
  </svg>
  <a class="print-link" href="#">Print this article</a>

  <figure class="photo-frame" style="left:171px;top:214px;width:226px;height:532px">
    <div class="photo sepia" role="img" aria-label="Air hostess smiling in an aircraft doorway"></div>
  </figure>
  <figure class="photo-frame" style="left:415px;top:214px;width:226px;height:252px">
    <div class="photo sepia-group" role="img" aria-label="Three sisters in air hostess uniforms with printed caption below"></div>
  </figure>

  <svg class="pointer" style="left:651px;top:424px" width="46" height="50" viewBox="0 0 46 50" fill="none" stroke="#999" stroke-width="1.3">
    <path d="M2 12 16 2v6c18 0 28 12 26 26-1 8-6 13-12 15 6-5 7-12 4-18-3-6-10-10-18-10v7z"/>
  </svg>

  <p class="caption-text" style="top:477px">This is probably something of a record--three sisters who are all air hostesses. They are the Hartley sisters.....Marguerite, Elva, and Rosalind, daughters of Mr and Mrs W. G. Hartley, Kenmore Road, Gisborne.</p>
  <p class="caption-text" style="top:585px">And this young lady, Doreen Astley, of Auckland, has made history in another way. She was the first air hostess to make a scheduled flight to Gisborne, on Sunday of last week. Hostess service has been extended by C.A.S. to include Gisborne flights, begin-ning with the Sunday Services.</p>

  <svg class="pointer" style="left:411px;top:694px" width="48" height="50" viewBox="0 0 48 50" fill="none" stroke="#999" stroke-width="1.3">
    <path d="M2 40 14 50v-6c18 0 30-10 30-24 0-9-5-16-12-20 5 6 5 13 2 19-3 7-11 11-20 11v-7z"/>
  </svg>

  <figure class="photo-frame" style="left:171px;top:760px;width:226px;height:132px">
    <div class="photo sepia-scene" role="img" aria-label="Old highway bridge across the Waiapu River with printed caption"></div>
  </figure>
  <h2 class="section-heading">BRIDGE IN SPLINTS</h2>
  <p class="caption-text" style="top:781px">The old highway bridge across the Waiapu River near Ruatoria probably has more Bailey "splints" than any other bridge in the country. It is to be replaced soon by a modern structure two miles downstream, after which all main-route traffic will pass through Ruatoria township. (Picture, Eastland).</p>
</main>

<div class="divider"></div>

<aside>
  <h2 class="side-title">ARCHIEVES</h2>
  <div class="page-thumb" role="img" aria-label="Scanned magazine spread with portrait photographs"></div>
  <a class="view-page" href="#">View Page</a>
  <div class="issue-tree">
    <span class="line"></span>
    <div class="root">
      <svg style="position:absolute;left:-2px;top:5px" width="14" height="10" viewBox="0 0 14 10" fill="none" stroke="#444"><path d="M0 5h12M8 1l4 4-4 4"/></svg>No.48</div>
    <ul>
      <li><svg width="20" height="10" viewBox="0 0 20 10" fill="none" stroke="#444"><path d="M0 5h18M14 1l4 4-4 4"/></svg>July 14, 1960</li>
      <li><svg width="20" height="10" viewBox="0 0 20 10" fill="none" stroke="#444"><path d="M0 5h18M14 1l4 4-4 4"/></svg>July 13, 1960</li>
      <li><svg width="20" height="10" viewBox="0 0 20 10" fill="none" stroke="#444"><path d="M0 5h18M14 1l4 4-4 4"/></svg>July 12, 1960</li>
      <li><svg width="20" height="10" viewBox="0 0 20 10" fill="none" stroke="#444"><path d="M0 5h18M14 1l4 4-4 4"/></svg>July 11, 1960</li>
      <li><svg width="20" height="10" viewBox="0 0 20 10" fill="none" stroke="#444"><path d="M0 5h18M14 1l4 4-4 4"/></svg>July 10, 1960</li>
      <li><svg width="20" height="10" viewBox="0 0 20 10" fill="none" stroke="#444"><path d="M0 5h18M14 1l4 4-4 4"/></svg>July 9, 1960</li>
    </ul>
  </div>

  <div class="cover" style="left:757px;top:596px">
    <div class="cover-art" role="img" aria-label="Colour cover: child dancing in a giant shell" style="background:linear-gradient(180deg,#3fa0c8,#b8aeb4 55%,#6b6f7a)"></div>
    <p class="cover-label">No. 77 November 3, 1960</p>
  </div>
  <div class="cover" style="left:898px;top:596px">
    <div class="cover-art" role="img" aria-label="Colour cover: woman with surfboard on a beach" style="background:linear-gradient(180deg,#6fb2d6,#a8c6d6 55%,#d8d2c2)"></div>
    <p class="cover-label">No. 77 November 3, 1960</p>
  </div>
  <div class="cover" style="left:757px;top:810px">
    <div class="cover-art" role="img" aria-label="Colour cover: girl in traditional dress before a carved house" style="background:linear-gradient(180deg,#7a4a3a,#5b3426 50%,#8a6a4a)"></div>
    <p class="cover-label">No. 77 November 3, 1960</p>
  </div>
  <div class="cover" style="left:898px;top:810px">
    <div class="cover-art" role="img" aria-label="Colour cover: friends in a convertible above a bay" style="background:linear-gradient(180deg,#7db7d8,#5f9a8e 45%,#d8d8d2)"></div>
    <p class="cover-label">No. 77 November 3, 1960</p>
  </div>
</aside>

<footer>
  <div class="footer-rule"></div>
  <div class="licence-badge" role="img" aria-label="Licence badge"></div>
  <p class="copyright">© 2012 Tairawhiti Heritage Library</p>
  <p class="build-code">Z4</p>
</footer>
</body>
</html>
```